Street Sign Project - Attract Customers

We need a street sign designed to display out the front of the building. It design will need to be 1800mm wide x 900mm high. We need to show potential customers where we are inviting. Some of the attachments are for inspiration. The sign will be printed on a sheet of aluminum. if you have a good look at our web site which is www.tv-r.com.au you should get a good feeling about the company and what we do.

Target Market(s)

Construction companies, landscaping and civil earth moving companies who may drive past our business

Industry/Entity Type

Building

Font styles to use
Sans Serif

Colors
ffffff
3277b5
000000

Requirements
Must have
• Company logo must be the main focus point
• The number "38" on the sign to show street number (300mm high)
• phone number - (02) 9413 5860
• web address - www.tv-r.com.au
• I have loaded pictures i would like to see used in the sign
Nice to have
• Banner picture as attached
Should not have
• Bright colours. Please use our blue colour where possible

```html
<!DOCTYPE html>
<html lang="en">
<head>
<meta charset="utf-8">
<title>Transvey &amp; Rigging Supplies – Street Sign</title>
<link rel="stylesheet" href="https://fonts.googleapis.com/css2?family=Archivo+Black&family=Montserrat:wght@600;700&family=Oswald:wght@500&display=swap">
<style>
  :root {
    --brand-blue: #1a509d;
    --white: #ffffff;
    --street-orange: #ee8222;
    --photo-steel: #8fa7c2;
    --photo-earth: #8b7d6a;
    --photo-light: #d9dde2;
    --photo-sky: #9fb8c9;
    --photo-red: #b5453a;
  }
  html, body {
    margin: 0;
    padding: 0;
    overflow: hidden;
    background: var(--white);
  }
  .sign {
    position: relative;
    width: 1200px;
    height: 601px;
    background: var(--brand-blue);
    overflow: hidden;
    font-family: "Montserrat", Arial, sans-serif;
  }
  .photo-strip {
    position: absolute;
    left: 29px;
    top: 18px;
    width: 672px;
    height: 144px;
    display: flex;
    gap: 3px;
    background: var(--white);
  }
  .photo-strip .photo { flex: 1; }
  .photo--conveyor { background: linear-gradient(160deg, #c9b497, var(--photo-steel)); }
  .photo--ramp     { background: linear-gradient(170deg, #5f6b4e, var(--photo-earth)); }
  .photo--hoist    { background: linear-gradient(180deg, #f2f2f2, var(--photo-light)); }
  .photo--chute    { background: linear-gradient(90deg, #c89a5c, #a8bccd, #c89a5c); }
  .photo--bucket   { background: linear-gradient(180deg, var(--photo-sky), #7fa6c4); }
  .photo--rolls    { background: linear-gradient(160deg, #c7a38a, var(--photo-red)); }

  .contact {
    position: absolute;
    left: 740px;
    top: 40px;
    width: 416px;
    text-align: center;
    color: var(--white);
    font-weight: 700;
  }
  .contact__phone {
    margin: 0;
    font-size: 50px;
    line-height: 58px;
    letter-spacing: 1px;
  }
  .contact__web {
    margin: 8px 0 0;
    font-size: 39px;
    line-height: 46px;
  }

  .company-name {
    position: absolute;
    left: 40px;
    top: 252px;
    width: 700px;
    margin: 0;
    text-align: center;
    color: var(--white);
    font-family: "Archivo Black", "Arial Black", sans-serif;
    font-weight: 400;
    text-transform: uppercase;
    line-height: 1;
  }
  .company-name__line {
    display: block;
    font-size: 72px;
    margin-bottom: 14px;
  }
  .company-name__suffix {
    display: block;
    font-size: 30px;
    letter-spacing: 2px;
  }

  .street-number {
    position: absolute;
    left: 790px;
    top: 202px;
    width: 410px;
    height: 399px;
  }
  .street-number__prefix {
    font-family: "Montserrat", Arial, sans-serif;
    font-weight: 600;
  }
  .street-number__digits {
    font-family: "Oswald", "Arial Narrow", sans-serif;
    font-weight: 500;
  }
</style>
</head>
<body>
  <main class="sign">
    <div class="photo-strip">
      <div class="photo photo--conveyor" role="img" aria-label="Photo of a curved roller conveyor carrying boxes"></div>
      <div class="photo photo--ramp" role="img" aria-label="Photo of a worker using a belt conveyor on an earthworks site"></div>
      <div class="photo photo--hoist" role="img" aria-label="Photo of a portable platform material hoist"></div>
      <div class="photo photo--chute" role="img" aria-label="Photo of a rubbish chute on scaffolding"></div>
      <div class="photo photo--bucket" role="img" aria-label="Photo of a concrete bucket lifted by a crane hoist"></div>
      <div class="photo photo--rolls" role="img" aria-label="Photo of a worker loading roofing rolls onto a hoist"></div>
    </div>

    <div class="contact">
      <p class="contact__phone">(02) 9413 5860</p>
      <p class="contact__web">www.tv-r.com.au</p>
    </div>

    <h1 class="company-name">
      <span class="company-name__line">Transvey</span>
      <span class="company-name__line">&amp; Rigging</span>
      <span class="company-name__line">Supplies</span>
      <span class="company-name__suffix">Pty Ltd</span>
    </h1>

    <svg class="street-number" viewBox="0 0 410 399" aria-label="Street number 38">
      <path d="M0 399 V165 A165 165 0 0 1 165 0 H410 V399 Z" fill="var(--white)"/>
      <text class="street-number__prefix" x="22" y="378" font-size="78" fill="var(--street-orange)">St</text>
      <text class="street-number__digits" x="108" y="382" font-size="440" textLength="272" lengthAdjust="spacingAndGlyphs" fill="var(--street-orange)">38</text>
    </svg>
  </main>
</body>
</html>
```